Volbrey Inc Business Card

Looking to get an updated business card for a Contract Machining company (www.volbreyinc.example) - looking for a clean design the portrays the technical nature of the business - colors can follow the website design and be in any combination that makes sense (red black, white, metallic or silver) - logos attached for use also. Would like space for: Name, title, business phone (555 214-3086), cell phone , website (www.volbreyinc.example) - possibly QR code could be integrated for website (designer choice), business address - 418 Harlow Bend, Alderwick, ST 48199 (cards will be for 4 employees, I will either need to modify a template or I can provide individual information)
Target Market(s)
Aerospace, defense and medical device manufacturing companies that need machining
Industry/Entity Type
Machining for aerospace, defense, medical
Contact Information for Business Card
Name, Title, Business Phone, Cell Phone, email, business website and business address
Look and feel

```html
<!DOCTYPE html>
<html lang="en">
<head>
<meta charset="utf-8">
<title>Volbrey Inc Business Card</title>
<link href="https://fonts.googleapis.com/css2?family=Montserrat:wght@800&family=Poppins:wght@400;500;700&display=swap" rel="stylesheet">
<style>
  :root {
    --brand-red: #c81f26;
    --brand-red-deep: #a91a22;
    --brand-red-light: #d9262d;
    --ink: #1d1d1f;
    --paper: #ffffff;
    --silver: #e4e4e6;
    --backdrop: #c9c9cb;
  }
  * { box-sizing: border-box; margin: 0; padding: 0; }
  html, body { width: 1200px; height: 900px; overflow: hidden; }
  body {
    background: var(--backdrop);
    font-family: "Poppins", sans-serif;
    position: relative;
  }
  .card {
    position: absolute;
    width: 700px;
    height: 400px;
    border-radius: 26px;
    overflow: hidden;
    box-shadow: 0 10px 24px rgba(0,0,0,0.22);
  }
  /* Front */
  .card-front {
    left: 70px; top: 45px;
    background: linear-gradient(135deg, var(--brand-red-light) 0%, var(--brand-red) 45%, var(--brand-red-deep) 100%);
  }
  .front-sheen {
    position: absolute; inset: 0;
    background: linear-gradient(115deg, rgba(255,255,255,0) 40%, rgba(255,255,255,0.08) 55%, rgba(255,255,255,0) 75%);
  }
  .front-brand {
    position: absolute; inset: 0;
    display: flex; flex-direction: column; align-items: center; justify-content: center;
    gap: 20px;
  }
  .front-brand .mark-circle {
    width: 160px; height: 160px; border-radius: 50%;
    background: var(--paper);
  }
  .front-brand .brand-name {
    font-family: "Montserrat", sans-serif; font-weight: 800;
    font-size: 52px; letter-spacing: 2px; line-height: 1; color: var(--paper);
  }
  /* Back */
  .card-back {
    left: 430px; top: 465px;
    background: linear-gradient(120deg, var(--paper) 0%, var(--paper) 48%, var(--silver) 78%, #f3f3f4 100%);
    color: var(--ink);
  }
  .back-brand {
    position: absolute; left: 46px; top: 38px;
    display: flex; align-items: center; gap: 22px;
  }
  .back-brand .mark-circle {
    width: 108px; height: 108px; border-radius: 50%;
    background: var(--brand-red);
  }
  .back-brand .brand-name {
    font-family: "Montserrat", sans-serif; font-weight: 800;
    font-size: 40px; letter-spacing: 1.5px; line-height: 1; color: var(--brand-red);
    margin-top: -36px;
  }
  .person { position: absolute; left: 62px; top: 172px; }
  .person-name {
    font-family: "Montserrat", sans-serif; font-weight: 800;
    font-size: 26px; color: var(--brand-red); text-transform: uppercase; line-height: 1.1;
  }
  .person-title { font-size: 19px; line-height: 1.3; }
  .contact-list {
    position: absolute; left: 62px; top: 256px;
    list-style: none; font-size: 17px; line-height: 29px;
  }
  .contact-list li { display: flex; align-items: center; gap: 12px; }
  .contact-list svg { width: 17px; height: 17px; flex: none; }
  .web-accent { color: var(--brand-red); }
  .address {
    position: absolute; right: 40px; top: 160px;
    text-align: right; font-size: 17px; line-height: 1.5; font-style: normal;
  }
</style>
</head>
<body>
  <section class="card card-front" aria-label="Business card front">
    <div class="front-sheen"></div>
    <div class="front-brand">
      <div class="mark-circle"></div>
      <div class="brand-name">VOLBREY</div>
    </div>
  </section>

  <section class="card card-back" aria-label="Business card back">
    <div class="back-brand">
      <div class="mark-circle"></div>
      <div class="brand-name">VOLBREY</div>
    </div>

    <div class="person">
      <div class="person-name">Marcus Delaney</div>
      <div class="person-title">Managing Director</div>
    </div>

    <ul class="contact-list">
      <li>
        <svg viewBox="0 0 24 24" fill="var(--brand-red)"><path d="M6.6 10.8a15 15 0 0 0 6.6 6.6l2.2-2.2a1 1 0 0 1 1-.25 11.4 11.4 0 0 0 3.6.57 1 1 0 0 1 1 1V20a1 1 0 0 1-1 1A17 17 0 0 1 3 4a1 1 0 0 1 1-1h3.5a1 1 0 0 1 1 1c0 1.25.2 2.45.57 3.57a1 1 0 0 1-.25 1z"/></svg>
        555 214-3086
      </li>
      <li>
        <svg viewBox="0 0 24 24" fill="none" stroke="var(--brand-red)" stroke-width="2"><rect x="6" y="2" width="12" height="20" rx="2"/><line x1="11" y1="18" x2="13" y2="18"/></svg>
        555 730-4412
      </li>
      <li>
        <svg viewBox="0 0 24 24" fill="var(--brand-red)"><path d="M2 5h20v14H2z"/><path d="M2 5l10 8 10-8" fill="none" stroke="#fff" stroke-width="1.6"/></svg>
        info@volbreyinc.example
      </li>
      <li>
        <svg viewBox="0 0 24 24" fill="none" stroke="var(--brand-red)" stroke-width="1.8"><circle cx="12" cy="12" r="9.5"/><ellipse cx="12" cy="12" rx="4.5" ry="9.5"/><line x1="2.5" y1="12" x2="21.5" y2="12"/></svg>
        <span>www.<span class="web-accent">volbreyinc</span>.example</span>
      </li>
    </ul>

    <address class="address">
      418 Harlow Bend<br>
      Alderwick, ST 48199
    </address>
  </section>
</body>
</html>
```